Logo, Web and Mobile Designs for enterprise social media platform

All the details are in the attached document, please start reading the scope document first which explains what is this project about and the details about the needed deliverables, after that please read the UI_Requirements document which will detail what is expected regarding the coded web version since this is a coded contest, it is very important that you meet the UI requirements or suggest something else but we will need to agree first before working on the coded version

Good Luck

Target Market(s)

Enterprise Social Media

Industry/Entity Type

Media

Coding

Coded - Design and coding required

Number of Pages Required

5+ page

Font styles to use
Sans Serif

Requirements
Must have
• All the must haves are listed in the scope document so please check before you start

```html
<!DOCTYPE html>
<html lang="en">
<head>
<meta charset="utf-8">
<title>Teamora – Timeline</title>
<link href="https://fonts.googleapis.com/css2?family=Roboto:wght@300;400;500;700&display=swap" rel="stylesheet">
<style>
:root{
  --orange:#e8730c;
  --orange-light:#f5a25a;
  --dark:#1c1c1c;
  --blue:#4a9fd8;
  --page:#f0f1f5;
  --white:#ffffff;
  --line:#e1e3e8;
  --text:#555a60;
  --muted:#9a9ea5;
  --heading:#2a2d31;
}
*{box-sizing:border-box;margin:0;padding:0}
html,body{width:1200px;height:2917px;overflow:hidden}
body{position:relative;background:var(--page);font-family:'Roboto',Arial,sans-serif;color:var(--text)}
.abs{position:absolute}

/* Header */
.site-header{left:0;top:0;width:1200px;height:152px;background:var(--dark);border-bottom:4px solid var(--orange)}
.brand{left:101px;top:30px;width:150px;text-align:center;color:var(--white)}
.brand-mark{width:46px;height:46px;border:2px solid var(--orange);margin:0 auto 6px}
.brand-name{font-size:24px;font-weight:500;letter-spacing:1px}
.search{left:352px;top:84px;width:467px;height:42px;background:var(--white);border-radius:21px;display:flex;align-items:center;padding:0 0 0 28px;font-size:14px;color:var(--muted)}
.search span{flex:1}
.search .search-btn{width:44px;height:100%;border-left:1px solid var(--line);display:flex;align-items:center;justify-content:center}
.btn{height:37px;border-radius:3px;color:var(--white);font-size:14px;font-weight:500;display:flex;align-items:center;justify-content:center;gap:6px;letter-spacing:.5px}
.btn-signup{left:895px;top:86px;width:97px;background:var(--orange)}
.btn-login{left:1004px;top:86px;width:97px;background:var(--blue)}
.header-icons{left:965px;top:22px;display:flex;gap:22px}
.header-icon{position:relative;width:32px;height:32px}
.badge{position:absolute;right:-8px;top:-6px;background:#e8412c;color:var(--white);font-size:10px;border-radius:9px;min-width:18px;height:18px;display:flex;align-items:center;justify-content:center}

/* Hero */
.hero{left:0;top:156px;width:1200px;height:589px;background:radial-gradient(ellipse at 42% 40%,#e9787a 0%,#f2b3b1 22%,#f6f6f4 48%,#eef0f2 100%)}
.hero-actions{left:788px;top:678px;width:321px;height:36px;background:var(--white);display:flex;align-items:center;font-size:13px;color:var(--text);box-shadow:0 1px 3px rgba(0,0,0,.15)}
.hero-actions span{flex:1;text-align:center;display:flex;align-items:center;justify-content:center;gap:6px}
.hero-actions .more{background:#4b4f55;color:var(--white);height:100%;flex:0 0 72px;letter-spacing:3px;font-weight:700}

/* Profile band */
.profile-band{left:0;top:745px;width:1200px;height:105px;background:var(--white);border-bottom:1px solid var(--line)}
.profile-avatar{left:97px;top:667px;width:200px;height:160px;background:var(--dark);border:4px solid var(--white);box-shadow:0 1px 4px rgba(0,0,0,.25);display:flex;flex-direction:column;align-items:center;justify-content:center;color:var(--white)}
.profile-avatar .mark{width:40px;height:40px;border:2px solid var(--orange);margin-bottom:8px}
.profile-avatar .name{font-size:19px;font-weight:500;letter-spacing:1px}
.profile-title{left:313px;top:762px}
.profile-title h1{font-size:17px;font-weight:500;color:var(--heading)}
.profile-title p{font-size:12px;color:var(--muted);margin-top:5px}
.tabs{left:648px;top:796px;width:461px;height:54px;display:flex;font-size:13px;color:var(--muted)}
.tabs span{flex:1;display:flex;align-items:center;justify-content:center}
.tabs .active{color:var(--orange);font-weight:500;border-bottom:3px solid var(--orange);background:#f6f7f9;border-top:1px solid var(--line)}

/* Cards */
.card{background:var(--white);border:1px solid var(--line)}
.composer{left:99px;top:885px;width:666px;height:105px;padding:16px 14px}
.composer-tools{display:flex;gap:22px;font-size:12.5px;color:var(--text);align-items:center}
.composer-tools i{display:inline-block;width:14px;height:14px;border:1.5px solid var(--orange);border-radius:2px;margin-right:6px;vertical-align:-2px}
.composer-tools .dots{color:var(--muted);letter-spacing:10px}
.composer-input{margin-top:16px;height:30px;border:1px solid #d4d7dc;font-size:12.5px;color:var(--muted);padding:7px 10px}

.post{left:99px;width:666px;height:552px}
.post-head{position:absolute;left:22px;top:20px;display:flex;gap:20px}
.post-avatar{width:62px;height:54px;background:var(--dark);display:flex;align-items:center;justify-content:center}
.post-avatar div{width:24px;height:24px;border:2px solid var(--orange)}
.post-meta{font-size:12.5px;padding-top:2px}
.post-meta .lead{color:var(--orange)}
.post-meta .time{color:var(--muted);margin-top:12px;font-size:12px}
.post-media{position:absolute;left:22px;top:94px;width:624px;height:268px;border:1px solid var(--line)}
.post-body{position:absolute;left:22px;top:388px;width:624px;font-size:12.5px;line-height:28px;color:#8b9096}
.post-body .ellipsis{color:var(--orange)}
.post-actions{position:absolute;left:0;bottom:0;width:100%;height:42px;border-top:1px solid var(--line);display:flex;font-size:12.5px;color:var(--muted)}
.post-actions span{display:flex;align-items:center;justify-content:center;border-right:1px solid var(--line);gap:6px}
.post-actions .w1{width:100px}.post-actions .w2{width:100px}.post-actions .w3{width:84px}.post-actions .w4{width:130px}.post-actions .w5{width:110px}
.post-actions .view{flex:1;border:none;color:var(--orange);font-weight:700}

/* Sidebar */
.about{left:790px;top:885px;width:311px;height:259px;padding:14px 15px}
.about h2{font-size:13.5px;font-weight:500;color:var(--heading);display:flex;justify-content:space-between;align-items:center}
.about .tag{font-size:10.5px;color:var(--muted);margin-top:8px}
.about .desc{font-size:12px;line-height:20px;margin-top:12px;padding-top:10px;border-top:1px solid var(--line)}
.about .desc b{color:var(--orange);font-weight:400}
.about ul{list-style:none;margin-top:12px;font-size:12px}
.about li{display:flex;align-items:center;gap:12px;height:29px}
.about li.link{color:var(--orange);font-weight:700}

.photos{left:790px;top:1183px;width:311px;height:270px;padding:14px 12px}
.photos h2{font-size:13px;color:var(--orange);font-weight:500;display:flex;gap:8px;align-items:center;padding-bottom:12px;border-bottom:1px solid var(--line)}
.photo-grid{display:grid;grid-template-columns:repeat(3,88px);gap:12px 11px;margin-top:12px}
.photo-grid div{height:84px}

.newsletter{left:790px;top:1494px;width:311px;height:177px;background:var(--orange);color:var(--white);padding:22px 30px}
.newsletter h2{font-size:17px;font-weight:500}
.newsletter p{font-size:11.5px;line-height:17px;margin-top:10px;color:#fde4cc}
.newsletter .nl-btn{margin-top:12px;width:148px;height:38px;background:#d9620a;border-radius:2px;display:flex;align-items:center;justify-content:center;gap:8px;font-size:15px}

.suggest{left:790px;top:1710px;width:311px;height:329px;padding:18px 16px}
.suggest h2{font-size:14px;font-weight:500;color:var(--heading)}
.suggest h2 small{font-size:11px;color:var(--blue);font-weight:400;margin-left:6px}
.suggest ul{list-style:none;margin-top:22px}
.suggest li{display:flex;align-items:center;gap:12px;height:49px}
.suggest .dot{width:24px;height:24px;border-radius:50%}
.suggest .name{font-size:13px;color:var(--heading);text-decoration:underline}
.suggest .handle{font-size:10px;color:var(--muted);margin-top:2px}
.tick{width:14px;height:14px;border-radius:50%;background:var(--orange);display:inline-flex;align-items:center;justify-content:center;margin-left:8px;vertical-align:-2px}

.progress{left:790px;top:2068px;width:311px;height:366px}
.progress h2{background:#2d3034;color:var(--white);font-size:15px;font-weight:400;height:40px;display:flex;align-items:center;justify-content:center}
.progress ul{list-style:none;padding:16px 18px}
.progress li{display:flex;gap:14px;height:75px}
.progress .face{width:50px;height:50px;border-radius:50%;background:#c99b82;flex:none}
.progress .label{font-size:12px;font-weight:500;color:var(--heading);margin-top:4px}
.progress .bar{height:18px;background:var(--orange);margin-top:10px}

/* Footer */
.site-footer{left:0;top:2820px;width:1200px;height:97px;background:#262626;color:#cfd1d4;font-size:13px}
.site-footer p{position:absolute;left:99px;top:40px}
.socials{position:absolute;left:896px;top:28px;display:flex;gap:16px}
.socials span{width:42px;height:42px;border:2px solid #cfd1d4;border-radius:50%}
</style>
</head>
<body>

<header class="abs site-header">
  <div class="abs brand">
    <div class="brand-mark"></div>
    <div class="brand-name">TEAMORA</div>
  </div>
  <div class="abs search"><span>Search</span>
    <div class="search-btn"><svg width="16" height="16" viewBox="0 0 16 16"><circle cx="7" cy="7" r="5" fill="none" stroke="#555" stroke-width="2"/><line x1="11" y1="11" x2="15" y2="15" stroke="#555" stroke-width="2"/></svg></div>
  </div>
  <div class="abs header-icons">
    <div class="header-icon"><svg width="32" height="32" viewBox="0 0 32 32" fill="#fff"><circle cx="12" cy="10" r="6"/><path d="M2 28c0-7 5-11 10-11s10 4 10 11z"/><circle cx="22" cy="11" r="5" opacity=".7"/><path d="M20 17c6 0 10 4 10 11h-6z" opacity=".7"/></svg></div>
    <div class="header-icon"><svg width="32" height="32" viewBox="0 0 32 32" fill="#fff"><path d="M3 6h18v12H10l-5 5v-5H3z"/><path d="M23 11h6v12h-2v4l-4-4h-9v-3h9z" opacity=".7"/></svg><span class="badge">33</span></div>
    <div class="header-icon"><svg width="32" height="32" viewBox="0 0 32 32"><circle cx="16" cy="16" r="12" fill="#fff"/><path d="M10 10c4 2 2 6 6 6s2 6 4 8M20 6c-2 4 2 6 6 6" stroke="#1c1c1c" stroke-width="2" fill="none"/></svg><span class="badge">15</span></div>
  </div>
  <div class="abs btn btn-signup"><svg width="12" height="12" viewBox="0 0 12 12" fill="#fff"><circle cx="6" cy="3.5" r="3"/><path d="M0 12c0-4 3-5.5 6-5.5s6 1.5 6 5.5z"/></svg>SIGN UP</div>
  <div class="abs btn btn-login"><svg width="11" height="12" viewBox="0 0 11 12" fill="#fff"><rect x="0" y="5" width="11" height="7"/><path d="M2.5 5V3.5a3 3 0 0 1 6 0V5" stroke="#fff" stroke-width="1.6" fill="none"/></svg>LOGIN</div>
</header>

<div class="abs hero" role="img" aria-label="Hand-drawn social media doodles around a red cloud with the brand name, hands holding devices and coffee cups on a white desk"></div>
<div class="abs hero-actions">
  <span>&#128077; Like</span><span>+ Follow</span><span>&#8618; Share</span><span class="more">•••</span>
</div>

<section class="abs profile-band"></section>
<div class="abs profile-avatar"><div class="mark"></div><div class="name">TEAMORA</div></div>
<div class="abs profile-title"><h1>Welcome TO Teamora</h1><p>There are many variations of passages of.</p></div>
<nav class="abs tabs"><span class="active">Timeline</span><span>Post text/files</span><span>Comment</span><span>Share</span><span>Like</span><span>More &#8964;</span></nav>

<div class="abs card composer">
  <div class="composer-tools"><span><i></i>Status</span><span><i></i>Photos</span><span><i></i>Place</span><span class="dots">••••</span></div>
  <div class="composer-input">What's on Your mind?</div>
</div>

<article class="abs card post" style="top:1021px">
  <div class="post-head"><div class="post-avatar"><div></div></div>
    <div class="post-meta"><div><span class="lead">It is a long established</span> fact that a reader when <span class="lead">https://teamora.net/</span></div><div class="time">3 minutes ago &#9673;</div></div></div>
  <div class="post-media" role="img" aria-label="Hands using a tablet and phone over a table covered in round social icons" style="background:linear-gradient(135deg,#a8734e,#3fa7c9 50%,#e06a3a)"></div>
  <p class="post-body">ere are many variations of passages of Lorem Ipsum available, but the majority have suffered alteration in some form, by injected humour, or randomised words which don't look even slightly believable. If you are going to use a passage of Lorem Ipsum, you need to be sure there isn't anything embarrassing hidden in the middle of text. All the Lorem Ipsum generators on the Internet tend to repeat predefined chunks <span class="ellipsis">[.....]</span></p>
  <div class="post-actions"><span class="w1">&#8630; Repaly</span><span class="w2">&#8644; Retweet</span><span class="w3">&#9829; Likes</span><span class="w4">&#128488; Comments</span><span class="w5">••• More</span><span class="view">VIEW MORE</span></div>
</article>

<article class="abs card post" style="top:1616px">
  <div class="post-head"><div class="post-avatar"><div></div></div>
    <div class="post-meta"><div><span class="lead">It is a long established</span> fact that a reader when <span class="lead">https://teamora.net/</span></div><div class="time">3 minutes ago &#9673;</div></div></div>
  <div class="post-media" role="img" aria-label="Glowing network of social icons around a hand with a thumbs up" style="background:linear-gradient(135deg,#5e8f8a,#b9d4cf 50%,#7d8f3f)"></div>
  <p class="post-body">ere are many variations of passages of Lorem Ipsum available, but the majority have suffered alteration in some form, by injected humour, or randomised words which don't look even slightly believable. If you are going to use a passage of Lorem Ipsum, you need to be sure there isn't anything embarrassing hidden in the middle of text. All the Lorem Ipsum generators on the Internet tend to repeat predefined chunks <span class="ellipsis">[.....]</span></p>
  <div class="post-actions"><span class="w1">&#8630; Repaly</span><span class="w2">&#8644; Retweet</span><span class="w3">&#9829; Likes</span><span class="w4">&#128488; Comments</span><span class="w5">••• More</span><span class="view">VIEW MORE</span></div>
</article>

<article class="abs card post" style="top:2212px">
  <div class="post-head"><div class="post-avatar"><div></div></div>
    <div class="post-meta"><div><span class="lead">It is a long established</span> fact that a reader when <span class="lead">https://teamora.net/</span></div><div class="time">3 minutes ago &#9673;</div></div></div>
  <div class="post-media" role="img" aria-label="Office desk with laptops and charts around a large orange social media sign" style="background:radial-gradient(ellipse at 50% 45%,#e8561c 0%,#e8561c 30%,#dfe3e8 60%,#9fb4c8 100%)"></div>
  <p class="post-body">ere are many variations of passages of Lorem Ipsum available, but the majority have suffered alteration in some form, by injected humour, or randomised words which don't look even slightly believable. If you are going to use a passage of Lorem Ipsum, you need to be sure there isn't anything embarrassing hidden in the middle of text. All the Lorem Ipsum generators on the Internet tend to repeat predefined chunks <span class="ellipsis">[.....]</span></p>
  <div class="post-actions"><span class="w1">&#8630; Repaly</span><span class="w2">&#8644; Retweet</span><span class="w3">&#9829; Likes</span><span class="w4">&#128488; Comments</span><span class="w5">••• More</span><span class="view">VIEW MORE</span></div>
</article>

<aside class="abs card about">
  <h2>SOCIAL MEDIA PLATFORM <span class="tick" style="width:20px;height:20px"><svg width="10" height="10" viewBox="0 0 10 10"><path d="M1 5l3 3 5-6" stroke="#fff" stroke-width="2" fill="none"/></svg></span></h2>
  <p class="tag">Lorem Ipsum is simply dummy text</p>
  <p class="desc">Connecting the world's professionals make them More productive and successful. using 'Content here content here', making look <b>@teamora.com</b></p>
  <ul>
    <li><svg width="12" height="14" viewBox="0 0 12 14"><path d="M6 0a5 5 0 0 0-5 5c0 4 5 9 5 9s5-5 5-9a5 5 0 0 0-5-5z" fill="#9a9ea5"/><circle cx="6" cy="5" r="2" fill="#fff"/></svg>Lorem Ipsum Dummy Locations</li>
    <li class="link"><svg width="13" height="13" viewBox="0 0 13 13"><path d="M5 8l3-3M3 7l-1.5 1.5a2 2 0 0 0 3 3L6 10M10 6l1.5-1.5a2 2 0 0 0-3-3L7 3" stroke="#9a9ea5" stroke-width="1.6" fill="none"/></svg>www.teamora.com</li>
    <li><svg width="13" height="13" viewBox="0 0 13 13"><rect x="0.5" y="2" width="12" height="10.5" fill="none" stroke="#9a9ea5"/><rect x="0.5" y="2" width="12" height="3" fill="#9a9ea5"/></svg>Joined October 2015</li>
  </ul>
</aside>

<aside class="abs card photos">
  <h2><svg width="14" height="12" viewBox="0 0 14 12"><rect y="2" width="14" height="10" rx="1" fill="#4a9fd8"/><circle cx="7" cy="7" r="3" fill="#fff"/></svg>1,052 Photo and Videos</h2>
  <div class="photo-grid">
    <div role="img" aria-label="Social network concept photo" style="background:linear-gradient(135deg,#2c3e5c,#6a88b0)"></div>
    <div role="img" aria-label="Colourful app icon cluster" style="background:linear-gradient(135deg,#1f6fb4,#f2a33a)"></div>
    <div role="img" aria-label="World map with network icons" style="background:linear-gradient(135deg,#3d8fd0,#a9d3f0)"></div>
    <div role="img" aria-label="Blue social icons on a device" style="background:linear-gradient(135deg,#1aa0c8,#74cbe0)"></div>
    <div role="img" aria-label="Social icons on a white background" style="background:linear-gradient(135deg,#e9eef2,#c95050)"></div>
    <div role="img" aria-label="Tree made of social icons on yellow" style="background:linear-gradient(135deg,#f3c51c,#f7d96a)"></div>
  </div>
</aside>

<aside class="abs newsletter">
  <h2>NEWSLETTER SIGN UP</h2>
  <p>Sign up now to get your using 'Content here, content here', making it look like readable.</p>
  <div class="nl-btn"><svg width="12" height="12" viewBox="0 0 12 12" fill="#fff"><circle cx="6" cy="3.5" r="3"/><path d="M0 12c0-4 3-5.5 6-5.5s6 1.5 6 5.5z"/></svg>SIGN UP</div>
</aside>

<aside class="abs card suggest">
  <h2>YOU MAY ALSO LIKE .<small>Refresh</small></h2>
  <ul>
    <li><span class="dot" style="background:#4285f4"></span><div><div class="name">Lookwise<span class="tick"><svg width="8" height="8" viewBox="0 0 10 10"><path d="M1 5l3 3 5-6" stroke="#fff" stroke-width="2" fill="none"/></svg></span></div><div class="handle">@lookwise</div></div></li>
    <li><span class="dot" style="background:#3aa3e3"></span><div><div class="name">Chatterly<span class="tick"><svg width="8" height="8" viewBox="0 0 10 10"><path d="M1 5l3 3 5-6" stroke="#fff" stroke-width="2" fill="none"/></svg></span></div><div class="handle">@chatterly</div></div></li>
    <li><span class="dot" style="background:#3b5a98"></span><div><div class="name">Friendhub<span class="tick"><svg width="8" height="8" viewBox="0 0 10 10"><path d="M1 5l3 3 5-6" stroke="#fff" stroke-width="2" fill="none"/></svg></span></div><div class="handle">@friendhub</div></div></li>
    <li><span class="dot" style="background:#c9222a"></span><div><div class="name">Pinboardly<span class="tick"><svg width="8" height="8" viewBox="0 0 10 10"><path d="M1 5l3 3 5-6" stroke="#fff" stroke-width="2" fill="none"/></svg></span></div><div class="handle">@pinboardly</div></div></li>
    <li><span class="dot" style="background:#1479b8"></span><div><div class="name">Linkpath Pulse<span class="tick"><svg width="8" height="8" viewBox="0 0 10 10"><path d="M1 5l3 3 5-6" stroke="#fff" stroke-width="2" fill="none"/></svg></span></div><div class="handle">@linkpathpulse</div></div></li>
  </ul>
</aside>

<aside class="abs card progress">
  <h2>PROGRESS BARS THIS WEEK</h2>
  <ul>
    <li><div class="face" role="img" aria-label="Member portrait"></div><div><div class="label">Established fact that a reader</div><div class="bar" style="width:210px"></div></div></li>
    <li><div class="face" role="img" aria-label="Member portrait" style="background:#b98a6e"></div><div><div class="label">Established fact that a reader</div><div class="bar" style="width:125px;background:#ef8a2e"></div></div></li>
    <li><div class="face" role="img" aria-label="Member portrait" style="background:#a6705a"></div><div><div class="label">Established fact that a reader</div><div class="bar" style="width:190px;background:var(--orange-light)"></div></div></li>
    <li><div class="face" role="img" aria-label="Member portrait" style="background:#8e7466"></div><div><div class="label">Established fact that a reader</div><div class="bar" style="width:72px;background:#f8bd86"></div></div></li>
  </ul>
</aside>

<footer class="abs site-footer">
  <p>© Copy Rights 2015 Teamora.all Right Reserved.</p>
  <div class="socials" aria-label="Social links"><span></span><span></span><span></span><span></span></div>
</footer>

</body>
</html>
```